Kinderbuchautor sucht emotionales Webdesign
Zielgruppe
Ich bin Autor von Kinderbüchern und suche jemanden,d er meine Website 'Kind- und Elterngerecht' gestalten kann und hier vielleicht gute Ideen oder bestenfalls schon Erfahrung hat.
Ich habe vor ein paar Jahren begonnen, Kinderbücher zu schreiben. Meine Bücher konzentrieren sich auf Kinder zwischen 0 und 12 Jahren. Ich schreibe auf Deutsch und auf Englisch und arbeite mit verschiedenen internationalen Illustratoren zusammen, mit denen ich immer neue Konzepte entwickele.
Formate sind u.a.
- Bilderbücher in verschiedenen Sprachen (insbes. Deutsch und Englisch, aber auch Spanisch, französisch und z.T. Chinesisch)
- Bilinguale Bilderbücher und Erstlese-Bücher (diese sind in der Tat zweisprachig)
- Romane für 8-12 jährige
- einsprachige Erstlese-Bücher
- Chapter Books (zwischen 60 und 100 Seiten)
Mit meinen Geschichten bin ich in erster Linie daran interessiert, neue Erfahrungen zu vermitteln und Anregungen für neue Perspektiven auf die Welt zu geben. Ich möchte das auf spielerische Weise tun, allerdings nicht zufällig. Das Schreiben aus der Perspektive der Kinder öffnet die Tür zu Welten, die von Elfen und Tieren, Meerjungfrauen und Königen, Zwergen und Riesen bevölkert sind – Wesen, die Probleme haben und sie lösen können, indem sie einfach die Beschränkungen unserer realen Welt umgehen. Das Mögliche zu entdecken, wo nichts wahrscheinlich erscheint.
Die Zielgruppe sind in erster Linie Eltern, Großeltern, Lehrer, Pädagogen etc.
Aufgabenstellung
Es geht bei dieser Website insbesondere darum, die richtige Emotion rüber zu bringen. Da viele Bücher zweisprachig sind oder die Bücher in verschiedenen Sprachen veröffentlicht werden, kann auch der Lerncharakter herausgestellt werden. Ich will allerdings nicht, dass die Website mit Lernhilfen für Pädagogen gespickt ist das ist nicht das Ziel. Das ganze soll den Fun-Faktor unterstreichen. Zum Beispiel gibt es in den USA fast eine große Anzahl von sog. 'Home-Learning' Initiativen, bei denen Kinder schon sehr früh mit. z.B. Hilfe von Bilderbüchern und leichten Erstlesebüchern andere Sprachen lernen, das ganze aber nicht als Lernprogramm sehen. Das ist einfach so, weil die Eltern aus zwei verschiedenen Kulturkreisen kommen. Das ist noch weitgehend eine Nische.
Aus diesem Grund werden die Bücher auch im internationalen Bereich, z.B. USA, Kanada, Spanien, Australien und UK vermarktet, neben D-A-CH.
Es gibt bereits eine Website, die aber NICHT als Vorlage genommen werden soll. Hier kann sich an den FARBEN orientiert werden: www.haraldwenke.com.
DIe Website wurde mit ZUPO erstellt. ZUPO ist aber keine zwingende Vorgabe. Es geht darum, die richtige Emotion zu kreieren.
Beipiele von Seiten, die mir hier gut gefallen, weil sie auch Social-Media optimiert sind, sind z.B. die folgenden:
http://dorvane.com/
https://www.melvinharrowgate.com/
http://www.lucasferndale.com/
Ich habe ein Logo, das ist ein Name 'Harald Wenke' mit der Schrift Luna Bar. Ich habe Illustrationen und Fotos sowie Cover der Bücher als Attachment beigefügt.

```html
<!DOCTYPE html>
<html lang="de">
<head>
<meta charset="utf-8">
<title>Harald Wenke – Kinderbuchautor</title>
<link href="https://fonts.googleapis.com/css2?family=Bangers&family=Roboto:wght@400;500;700&display=swap" rel="stylesheet">
<style>
:root{
  --red:#d6220f;
  --ink:#222;
  --dark:#2d2d2f;
  --olive:#8f8a1f;
  --blue:#4f8dd0;
  --green:#7a9e0a;
  --salmon:#d4644f;
  --orange:#e07a35;
  --teal:#2b7fa0;
  --footer:#2d2d2d;
  --white:#fff;
}
*{margin:0;padding:0;box-sizing:border-box}
html,body{width:1200px;height:3734px;overflow:hidden}
body{font-family:"Roboto",sans-serif;color:var(--ink);background:var(--white);position:relative}
.display{font-family:"Bangers",sans-serif;font-weight:400;text-transform:uppercase;letter-spacing:1px;white-space:nowrap}

/* header */
.site-header{position:absolute;top:0;left:0;width:1200px;height:52px;background:var(--white);box-shadow:0 2px 6px rgba(0,0,0,.15);z-index:5}
.brand{position:absolute;left:94px;top:10px;font-weight:500;font-size:26px;color:#555}
.nav{position:absolute;left:472px;top:17px;display:flex;gap:18px;font-size:16px;font-weight:500;color:var(--ink);white-space:nowrap}
.nav .active{color:var(--red)}
.lang{position:absolute;left:1050px;top:17px;font-size:16px;font-weight:500;color:#999}

/* hero */
.hero{position:absolute;top:52px;left:0;width:1200px;height:675px;background:linear-gradient(120deg,#e8d9a8 0%,#c9b678 35%,#8a8a55 60%,#d8cfa2 100%)}
.hero-quote{position:absolute;left:488px;top:128px;font-size:44px;line-height:46px;color:#22331a}
.hero-tag{position:absolute;left:497px;top:232px;width:532px;height:24px;background:var(--red);color:var(--white);font-weight:700;font-size:18px;line-height:24px;padding-left:6px;white-space:nowrap}
.hero-arrow{position:absolute;top:335px}
.hero-figure{position:absolute;left:637px;top:300px;width:377px;height:461px;border-radius:20px;background:linear-gradient(160deg,#f2a9cc,#e7d3b6 55%,#c8a474);opacity:.9}

/* works */
.works-title{position:absolute;top:796px;left:0;width:1200px;text-align:center;font-size:44px;line-height:50px;color:var(--ink)}
.works-underline{position:absolute;top:846px;left:397px;width:406px;height:3px;background:var(--red)}
.book{position:absolute;top:872px;width:152px;text-align:center}
.book .cover{width:152px;height:197px;display:block}
.book p{margin-top:7px;font-size:13.5px;font-weight:500;line-height:16px}
.btn{display:inline-flex;align-items:center;gap:10px;background:var(--red);color:var(--white);font-family:"Bangers",sans-serif;text-transform:uppercase;letter-spacing:1px;white-space:nowrap;height:36px;padding:0 10px;font-size:22px;line-height:36px}
.btn svg{width:12px;height:20px;flex:none}
.newsletter-wrap{position:absolute;left:0;top:1143px;width:1200px;text-align:center}

/* feature rows */
.row{position:absolute;left:0;width:1200px;height:343px}
.row .photo{position:absolute;top:0;width:603px;height:343px}
.row .text{position:absolute;top:0;width:597px;height:343px;color:var(--white);padding:66px 40px 0 42px}
.row .text.left{left:0;width:603px;padding-left:126px}
.row .text.right{left:603px}
.row .photo.left{left:0}
.row .photo.right{left:603px;width:597px}
.row h2{font-size:24px;line-height:30px;margin-bottom:4px}
.row p{font-size:13.5px;line-height:22.5px;margin-bottom:22px;white-space:nowrap}

/* bottom trio */
.trio{position:absolute;top:3175px;left:0;width:1200px;height:481px}
.gratis{position:absolute;left:0;top:0;width:429px;height:481px;background:linear-gradient(170deg,#b8d8ee 0%,#8ec0e4 40%,#7460c0 80%,#4a3a8a 100%)}
.gratis h3{position:absolute;left:178px;top:34px;font-size:44px;line-height:50px;color:var(--ink)}
.gratis .underline{position:absolute;left:178px;top:88px;width:130px;height:3px;background:var(--red)}
.gratis p{position:absolute;left:178px;top:104px;font-size:17px;line-height:22px;color:var(--ink);white-space:nowrap}
.gratis .btn{position:absolute;left:178px;top:180px}
.follow{position:absolute;left:429px;top:0;width:342px;height:481px;background:var(--teal)}
.follow h3{position:absolute;left:0;top:34px;width:342px;text-align:center;font-size:42px;line-height:50px;color:var(--white)}
.follow .underline{position:absolute;left:36px;top:88px;width:270px;height:3px;background:var(--white)}
.fb-box{position:absolute;left:0;top:114px;width:342px;height:92px;background:linear-gradient(135deg,#6d8fa5,#c9b79a)}
.fb-box .name{position:absolute;left:56px;top:10px;color:var(--white);font-size:15px;white-space:nowrap}
.fb-box .count{position:absolute;left:56px;top:28px;color:var(--white);font-size:10px}
.fb-box .like{position:absolute;left:6px;top:68px;width:100px;height:18px;background:#f2f2f2;font-size:10px;line-height:18px;padding-left:8px;color:#333}
.fb-box .share{position:absolute;right:10px;top:68px;width:50px;height:18px;background:#f2f2f2;font-size:10px;line-height:18px;text-align:center;color:#333}
.fb-box .avatar{position:absolute;left:10px;top:10px;width:38px;height:38px;background:#b9a27c}
.fb-foot{position:absolute;left:8px;top:212px;width:326px;height:30px;background:var(--white);font-size:10px;line-height:30px;padding-left:8px;color:#444;white-space:nowrap}
.insta-photo{position:absolute;left:0;top:252px;width:342px;height:229px;background:linear-gradient(160deg,#c93b2f,#e6d3a0 60%,#3a5ea8)}
.insta-btn{position:absolute;left:236px;top:50px;width:64px;height:64px;background:var(--teal);border-radius:12px}
.contact{position:absolute;left:771px;top:0;width:429px;height:481px;background:var(--red);color:var(--white)}
.contact h3{position:absolute;left:0;top:34px;width:429px;text-align:center;font-size:44px;line-height:50px}
.contact .underline{position:absolute;left:145px;top:88px;width:140px;height:3px;background:var(--white)}
.contact .lead{position:absolute;left:0;top:108px;width:429px;text-align:center;font-size:17px;font-weight:500;white-space:nowrap}
.field{position:absolute;left:62px;width:310px;height:30px;background:var(--white);color:#888;font-size:16px;line-height:30px;padding-left:14px}
.field.msg{height:122px;line-height:26px;padding-top:4px}
.send{position:absolute;left:170px;top:410px;display:flex;align-items:center;gap:10px;font-size:34px;line-height:40px}
.send svg{width:18px;height:30px}

.site-footer{position:absolute;top:3656px;left:0;width:1200px;height:78px;background:var(--footer);color:var(--white);text-align:center;font-size:14px;line-height:66px}
</style>
</head>
<body>

<header class="site-header">
  <div class="brand">Harald Wenke</div>
  <nav class="nav">
    <span class="active">HOME</span><span>ÜBER MICH</span><span>BÜCHER</span><span>GRATIS!</span><span>KONTAKT</span><span>NEWSLETTER</span>
  </nav>
  <div class="lang">DE | EN</div>
</header>

<section class="hero" role="img" aria-label="Foto: lachendes Kleinkind mit Buch auf einer Holzbank im Sonnenlicht"></section>
<div class="hero-figure" role="img" aria-label="Illustration: Igel malt einen Regenbogen an der Staffelei"></div>
<div class="hero-quote display">„Ein neuer Blick auf die Welt,<br>&nbsp;phantastisch &amp; magisch“</div>
<div class="hero-tag">HARALD WENKE, KINDERBUCHAUTOR</div>
<svg class="hero-arrow" style="left:94px" width="36" height="62" viewBox="0 0 36 62"><path d="M34 2 L2 31 L34 60 Z" fill="var(--red)"/></svg>
<svg class="hero-arrow" style="left:1070px" width="36" height="62" viewBox="0 0 36 62"><path d="M2 2 L34 31 L2 60 Z" fill="var(--red)"/></svg>

<h1 class="works-title display">Meine neuesten Werke</h1>
<div class="works-underline"></div>

<div class="book" style="left:131px"><div class="cover" role="img" aria-label="Buchcover: Schwein mit Geburtstagstorte" style="background:linear-gradient(#f4efe3,#e8b96a 60%,#a66b3a)"></div><p>Paula Pig's Jolly<br>Party Day</p></div>
<div class="book" style="left:327px"><div class="cover" role="img" aria-label="Buchcover: bunte Malerlandschaft" style="background:linear-gradient(#bfe4f2,#f2a6c8 40%,#6fae4a)"></div><p>Rosy The Artist</p></div>
<div class="book" style="left:522px"><div class="cover" role="img" aria-label="Buchcover: Igel im Wald" style="background:linear-gradient(#cfe8f0,#b6d46c 50%,#8a6a2e)"></div><p>Hustle-Bustle and the<br>Shining Pearls</p></div>
<div class="book" style="left:718px"><div class="cover" role="img" aria-label="Buchcover: Tiere auf einem Floß im Fluss" style="background:linear-gradient(#fff,#bfe2f5 45%,#4aa0d8)"></div><p>Creek Boat<br>The Creek Raft</p></div>
<div class="book" style="left:914px"><div class="cover" role="img" aria-label="Buchcover: Tiere am Waldrand" style="background:linear-gradient(#fff,#cde7c0 45%,#5b9a3a)"></div><p>Creek Boat<br>The Clumsy Badger</p></div>

<div class="newsletter-wrap"><a class="btn">Newsletter bestellen <svg viewBox="0 0 12 20"><path d="M1 1 L11 10 L1 19 Z" fill="none" stroke="#fff" stroke-width="2"/></svg></a></div>

<section class="row" style="top:1222px">
  <div class="photo left" role="img" aria-label="Foto: Autor mit Schiebermütze hält eine rote Clownsnase vor das Auge" style="background:linear-gradient(120deg,#3a3a3a,#8a6b58 55%,#2a2a2a)"></div>
  <div class="text right" style="background:var(--dark);padding-top:22px">
    <h2 class="display">Hallo!</h2>
    <p>Willkommen auf meiner Website... Danke für Deine Zeit!<br>Du bist dabei, mehr über meine Bücher und mich selbst zu erfahren.<br>Finde heraus, was es Neues bei mir gibt.</p>
    <p>Viel Spaß!</p>
    <a class="btn">Mehr über mich erfahren <svg viewBox="0 0 12 20"><path d="M1 1 L11 10 L1 19 Z" fill="none" stroke="#fff" stroke-width="2"/></svg></a>
  </div>
</section>

<section class="row" style="top:1465px">
  <div class="text left" style="background:var(--olive)">
    <h2 class="display">Bilderbücher in verschiedenen Sprachen</h2>
    <p>Lorem ipsum dolor sit amet, consetetur sadipscing elitr, sed diam<br>nonumy eirmod tempor invidunt ut labore et dolore magna aliquyam<br>erat, sed diam voluptua.</p>
    <p>At vero eos et accusam et justo duo dolores et ea rebum. Stet clita<br>kasd gubergren, no sea takimata sanctus est Lorem ipsum.</p>
    <a class="btn">Mehr erfahren <svg viewBox="0 0 12 20"><path d="M1 1 L11 10 L1 19 Z" fill="none" stroke="#fff" stroke-width="2"/></svg></a>
  </div>
  <div class="photo right" role="img" aria-label="Foto: Großmutter liest zwei Kindern ein Bilderbuch vor" style="background:linear-gradient(120deg,#2f2a28,#8aa33a 45%,#2a3550 75%,#b07a48)"></div>
</section>

<section class="row" style="top:1807px">
  <div class="photo left" role="img" aria-label="Foto: Kind liest ein aufgeschlagenes Bilderbuch" style="background:linear-gradient(120deg,#3a3530,#e8e6e2 50%,#c9a060)"></div>
  <div class="text right" style="background:var(--blue)">
    <h2 class="display">Bilinguale Bilderbücher und Erstlese-Bücher</h2>
    <p>Duis autem vel eum iriure dolor in hendrerit in vulputate velit esse<br>molestie consequat, vel illum dolore eu feugiat nulla facilisis at vero<br>eros et accumsan et iusto odio dignissim qui blandit praesent.</p>
    <p>Luptatum zzril delenit augue duis dolore te feugait nulla facilisi.<br>Lorem ipsum dolor sit amet, consectetuer adipiscing eliterat volutpat.</p>
    <a class="btn">Mehr erfahren <svg viewBox="0 0 12 20"><path d="M1 1 L11 10 L1 19 Z" fill="none" stroke="#fff" stroke-width="2"/></svg></a>
  </div>
</section>

<section class="row" style="top:2149px">
  <div class="text left" style="background:var(--green)">
    <h2 class="display">Einsprachige Erstlese-Bücher</h2>
    <p>Ut wisi enim ad minim veniam, quis nostrud exerci tation ullamcorper<br>suscipit lobortis nisl ut aliquip ex ea commodo consequat.</p>
    <p>Duis autem vel eum iriure dolor in hendrerit in vulputate velit esse<br>molestie consequat, vel illum dolore eu feugiat nulla facilisis at vero<br>eros et accumsan et iusto odio dignissim qui blandit praesent.</p>
    <a class="btn">Mehr erfahren <svg viewBox="0 0 12 20"><path d="M1 1 L11 10 L1 19 Z" fill="none" stroke="#fff" stroke-width="2"/></svg></a>
  </div>
  <div class="photo right" role="img" aria-label="Foto: rote Holzbuchstaben im Gras" style="background:linear-gradient(140deg,#2e4a14,#6f9a2a 45%,#c8443a 65%,#3c5a1a)"></div>
</section>

<section class="row" style="top:2491px">
  <div class="photo left" role="img" aria-label="Foto: Mädchen mit Sonnenhut liest ein Buch auf einer Bank" style="background:linear-gradient(120deg,#4a5a2e,#e9d6c6 45%,#d8a2a8 70%,#6a4a30)"></div>
  <div class="text right" style="background:var(--salmon)">
    <h2 class="display">Romane für 8-12 Jährige</h2>
    <p>Nam liber tempor cum soluta nobis eleifend option congue nihil<br>imperdiet doming id quod mazim placerat facer possim assum.</p>
    <p>Lorem ipsum dolor sit amet, consectetuer adipiscing elit, sed diam<br>nonummy nibh euismod tincidunt ut laoreet dolore magna aliquam<br>erat volutpat. Ut wisi enim ad minim veniam, quis nostrud exercico.</p>
    <a class="btn">Mehr erfahren <svg viewBox="0 0 12 20"><path d="M1 1 L11 10 L1 19 Z" fill="none" stroke="#fff" stroke-width="2"/></svg></a>
  </div>
</section>

<section class="row" style="top:2833px">
  <div class="text left" style="background:var(--orange)">
    <h2 class="display">Chapter Books</h2>
    <p>At vero eos et accusam et justo duo dolores et ea rebum. Stet clita<br>kasd gubergren, no sea takimata sanctus est Lorem ipsum dolor sit<br>amet. Lorem ipsum dolor sit amet, consetetur sadipscing elitr.</p>
    <p>Sed diam nonumy eirmod tempor invidunt ut labore et dolore magna<br>aliquyam erat, sed diam voluptua. At vero eos et accusam et justo.</p>
    <a class="btn">Mehr erfahren <svg viewBox="0 0 12 20"><path d="M1 1 L11 10 L1 19 Z" fill="none" stroke="#fff" stroke-width="2"/></svg></a>
  </div>
  <div class="photo right" role="img" aria-label="Foto: Mädchen pustet Seifenblasen" style="background:linear-gradient(120deg,#6a3a22,#d9a88a 45%,#b86b4a 70%,#4a2a1a)"></div>
</section>

<section class="trio">
  <div class="gratis" role="img" aria-label="Illustration: gemaltes lila Fabelwesen auf blauem Grund mit Geschenkschleife">
    <h3 class="display">Gratis!</h3>
    <div class="underline"></div>
    <p>Leseproben, Malvorlagen<br>und viele weitere Extras<br>zu meinen Geschichten</p>
    <a class="btn">Mehr erfahren <svg viewBox="0 0 12 20"><path d="M1 1 L11 10 L1 19 Z" fill="none" stroke="#fff" stroke-width="2"/></svg></a>
  </div>
  <div class="follow">
    <h3 class="display">Folgen Sie mir</h3>
    <div class="underline"></div>
    <div class="fb-box" role="img" aria-label="Titelbild der Autorenseite mit Illustration">
      <div class="avatar"></div>
      <div class="name">Kinderbuchautor Harald Wenke</div>
      <div class="count">975 „Gefällt mir“-Angaben</div>
      <div class="like">Seite gefällt mir</div>
      <div class="share">Teilen</div>
    </div>
    <div class="fb-foot">Sei der/die Erste deiner Freunde, dem/der das gefällt</div>
    <div class="insta-photo" role="img" aria-label="Foto: Junge mit Brille vor einem Bücherregal">
      <div class="insta-btn"></div>
    </div>
  </div>
  <div class="contact">
    <h3 class="display">Kontakt</h3>
    <div class="underline"></div>
    <div class="lead">Ich freue mich, von Ihnen zu hören!</div>
    <div class="field" style="top:142px">Name</div>
    <div class="field" style="top:182px">E-Mail</div>
    <div class="field" style="top:222px">Betreff</div>
    <div class="field msg" style="top:262px">Nachricht</div>
    <div class="send display">Abschicken <svg viewBox="0 0 18 30"><path d="M2 2 L16 15 L2 28 Z" fill="none" stroke="#fff" stroke-width="2.5"/></svg></div>
  </div>
</section>

<footer class="site-footer">Impressum</footer>

</body>
</html>
```